Brightlane Rapid Rinse Web Design

We are looking for a web design that highlights our state of the art fully automated commercial vehicle washing equipment. Similar system to a car wash however this system is meant for the largest vehicles on our roadways. Transport trucks with or without a trailer, busses both highway and school, RV's from 5th wheel type to A Class. Cement trucks, dump trucks, vac trucks, fuel trucks etc. Pick ups with utility trailers...Refrigerator truck clean outs.
Brightlane Rapid Rinse will wash your vehicle quickly and with a minimal impact on the environment

Home page
About us
Why Brightlane
Services and pricing
Videos of wash system
Fleets
contact us

Target Market(s)

Commercial vehicle owners and operators as well as corporate fleets. Includes busses, municipal, school and highway.both school and

Industry/Entity Type

transportation

Coding

Coded - Design and coding required

Number of Pages Required

5+ page

Font styles to use
Sans Serif

Colors
0054AA
0677BA
7BADD7
CADEEF
E8F1F8

Requirements
Must have
• Welcome page,why us page which describes the financial and environmental benefits. payment processing page, contact us page, Services which is washing vehicles and greasing for commercial vehicles that want that service and grease
Nice to have
• pictures of both clean and dirty commercial vehicles ie. before and after

```html
<!DOCTYPE html>
<html lang="en">
<head>
<meta charset="utf-8">
<title>Brightlane Rapid Rinse</title>
<link href="https://fonts.googleapis.com/css2?family=Montserrat:wght@500;600;700;800&family=Lato:wght@400;700&display=swap" rel="stylesheet">
<style>
:root{
  --blue:#0054AA;
  --blue-mid:#0677BA;
  --blue-soft:#7BADD7;
  --blue-pale:#CADEEF;
  --blue-mist:#E8F1F8;
  --white:#ffffff;
  --ink:#333a44;
  --muted:#5c6470;
  --black:#050505;
}
*{margin:0;padding:0;box-sizing:border-box}
html,body{width:1200px;height:4605px;overflow:hidden}
body{font-family:"Lato",Arial,sans-serif;color:var(--ink);background:var(--white);position:relative}
.head-font{font-family:"Montserrat",Arial,sans-serif}
section,header,footer,nav{position:absolute;left:0;width:1200px}
.abs{position:absolute}
svg{display:block}

/* top bar */
.topbar{top:0;height:66px;background:var(--blue);color:var(--white)}
.topbar .info{position:absolute;top:16px;display:flex;gap:10px;align-items:center;font-size:13px;line-height:16px}
.topbar .info b{font-family:"Montserrat",sans-serif;font-weight:600;display:block;font-size:13px}
.topbar .contact-btn{position:absolute;left:964px;top:18px;width:121px;height:36px;background:var(--white);color:var(--black);font:700 14px "Montserrat",sans-serif;display:flex;align-items:center;justify-content:center}

/* nav */
.mainnav{top:66px;height:68px;background:var(--white);border-bottom:1px solid var(--blue-mist)}
.brand{position:absolute;left:110px;top:6px;width:230px;text-align:center;font:700 27px/29px "Montserrat",sans-serif;color:var(--blue)}
.navlinks{position:absolute;right:115px;top:26px;display:flex;gap:28px;font-size:14px;color:var(--black)}

/* hero */
.hero{top:134px;height:617px;background:linear-gradient(90deg,#2d5a9a 0%,#4f79b3 30%,#8c9cb4 55%,#9aa1ab 70%,#7c828c 100%)}
.hero-photo{position:absolute;inset:0;background:
  linear-gradient(90deg,rgba(10,50,120,.65) 0%,rgba(20,70,150,.35) 45%,rgba(0,0,0,0) 60%),
  linear-gradient(90deg,transparent 62%,#b8232e 63%,#241d26 66%,#b8232e 70%,transparent 71%,transparent 91%,#b8232e 92%,#241d26 95%,#b8232e 98%),
  linear-gradient(180deg,#8a93a0 0%,#a8adb5 60%,#6d7079 100%)}
.hero-copy{position:absolute;left:111px;top:180px;color:var(--white);font-family:"Montserrat",sans-serif}
.hero-copy .kicker{font-weight:700;font-size:25px}
.hero-copy h1{font-weight:800;font-size:42px;line-height:54px;margin-top:6px}
.hero-copy .tag{font-weight:700;font-size:20px;margin-top:14px}
.btn{display:flex;align-items:center;justify-content:center;font:700 15px "Montserrat",sans-serif;letter-spacing:.3px}
.btn-white{background:var(--white);color:var(--blue)}
.btn-blue{background:var(--blue);color:var(--white)}
.hero .play{position:absolute;left:543px;top:396px;width:44px;height:44px;border-radius:50%;background:var(--blue-pale);display:flex;align-items:center;justify-content:center}

/* section headings */
.sec-title{position:absolute;left:0;width:1200px;text-align:center;font:700 35px "Montserrat",sans-serif;color:var(--blue)}
.sec-title.light{color:var(--white)}
.rule{position:absolute;left:518px;width:164px;height:7px;border-radius:4px;background:var(--blue)}
.rule.light{background:var(--white)}

/* about */
.about{top:751px;height:465px}
.about p{position:absolute;left:100px;top:148px;width:1000px;text-align:center;font-size:16.5px;line-height:37.5px;color:var(--black)}

/* services */
.services{top:1216px;height:756px;background:linear-gradient(160deg,#1d5fb0 0%,#0a54aa 40%,#0d4f9e 70%,#1a5fae 100%)}
.card{position:absolute;top:163px;width:316px;height:441px;background:var(--white);border-radius:6px;text-align:center}
.card .photo{position:absolute;left:7px;top:7px;width:302px;height:195px;border-radius:3px}
.card .badge{position:absolute;left:119px;top:170px;width:78px;height:78px;border-radius:50%;background:var(--blue);border:4px solid var(--white);display:flex;align-items:center;justify-content:center}
.card h3{position:absolute;top:262px;width:100%;font:700 19px "Montserrat",sans-serif;color:var(--blue)}
.card .bar{position:absolute;left:138px;top:295px;width:40px;height:3px;background:var(--blue)}
.card p{position:absolute;left:38px;top:313px;width:240px;font-size:15px;line-height:20px;color:var(--muted)}
.card .more{position:absolute;left:0;top:402px;width:100%;display:flex;justify-content:center;align-items:center;gap:10px;font:500 14px "Montserrat",sans-serif;color:var(--blue)}

/* before after */
.beforeafter{top:1972px;height:456px}
.ba-photo{position:absolute;top:0;width:600px;height:456px}
.ba-label{position:absolute;top:411px;height:45px;width:439px;background:var(--blue);color:var(--white);font:700 25px "Montserrat",sans-serif;letter-spacing:1.5px;display:flex;align-items:center;justify-content:center}

/* reviews */
.reviews{top:2428px;height:612px}
.review{position:absolute;top:204px;width:256px;height:247px;background:var(--white);box-shadow:0 2px 12px rgba(0,0,0,.12);text-align:center}
.review .avatar{position:absolute;left:88px;top:-38px;width:80px;height:80px;border-radius:50%;border:4px solid var(--blue);background:radial-gradient(circle at 50% 40%,#d9b9a2 0%,#8a6a55 55%,#3c3a44 100%)}
.review h4{position:absolute;top:62px;width:100%;font:500 18px "Montserrat",sans-serif;color:var(--blue)}
.review .sub{position:absolute;top:89px;width:100%;font:700 12px "Lato",sans-serif;color:var(--black)}
.review p{position:absolute;left:24px;top:112px;width:208px;font-size:13.5px;line-height:20px;color:var(--muted)}
.review .stars{position:absolute;top:200px;width:100%;color:var(--blue);font-size:18px;letter-spacing:2px}

/* mission */
.mission{top:3040px;height:545px;background:var(--blue);overflow:hidden}
.mission-photo{position:absolute;left:600px;top:0;width:600px;height:545px;background:
  linear-gradient(90deg,var(--blue) 0%,rgba(0,84,170,.4) 25%,rgba(0,84,170,0) 45%),
  linear-gradient(180deg,#6b8fbf 0%,#c9d3df 50%,#7f8fa6 100%)}
.goal{position:absolute;left:120px;width:342px;text-align:right;color:var(--white);font-size:15px;line-height:20px}
.goal-num{position:absolute;left:481px;width:54px;height:54px;border-radius:50%;background:var(--white);color:var(--blue);font:italic 800 24px "Montserrat",sans-serif;display:flex;align-items:center;justify-content:center}

/* contact */
.contact{top:3585px;height:640px}
.field{position:absolute;border:1px solid #9aa3ad;background:var(--white);font-size:11px;color:var(--ink);padding:0 16px;display:flex;align-items:center}
.field.area{align-items:flex-start;padding-top:18px}

/* footer */
.footer{top:4225px;height:380px;background:var(--black);color:var(--white)}
.footer .flogo{position:absolute;left:59px;top:60px;font:700 30px/43px "Montserrat",sans-serif}
.social{position:absolute;top:199px;width:32px;height:32px;border-radius:50%;background:var(--white)}
.fcol{position:absolute;top:60px}
.fcol h5{font:700 23px "Montserrat",sans-serif;letter-spacing:.5px}
.fcol ul{list-style:none;margin-top:21px}
.fcol li{font:500 16px/35px "Montserrat",sans-serif}
.fcol.links li{text-decoration:underline}
.fcontact{position:absolute;left:853px;top:60px}
.fcontact .row{position:absolute;left:14px;display:flex;gap:18px;align-items:flex-start;font:500 16px/25px "Montserrat",sans-serif;width:300px}
.fcontact .ic{width:30px;height:30px;border-radius:50%;background:var(--white);flex:none;display:flex;align-items:center;justify-content:center}
.footer .divider{position:absolute;left:111px;top:304px;width:978px;height:1px;background:#777}
.footer .copy{position:absolute;top:330px;width:100%;text-align:center;font:500 16px "Montserrat",sans-serif}
</style>
</head>
<body>

<header class="topbar">
  <div class="info" style="left:110px">
    <svg width="28" height="28" viewBox="0 0 28 28"><circle cx="14" cy="14" r="14" fill="#fff"/><path d="M10 8l3 3-2 2c1 2 2 3 4 4l2-2 3 3-2 2c-5 0-10-5-10-10z" fill="#0054AA"/></svg>
    <div><b>CONTACT</b>+1 555 010 0199</div>
  </div>
  <div class="info" style="left:330px">
    <svg width="28" height="28" viewBox="0 0 28 28"><circle cx="14" cy="14" r="14" fill="#fff"/><rect x="7" y="9" width="14" height="10" fill="none" stroke="#0054AA" stroke-width="2"/><path d="M7 9l7 6 7-6" fill="none" stroke="#0054AA" stroke-width="2"/></svg>
    <div><b>E-MAIL</b>rinse.desk@example.com</div>
  </div>
  <div class="info" style="left:600px">
    <svg width="28" height="28" viewBox="0 0 28 28"><circle cx="14" cy="14" r="14" fill="#fff"/><circle cx="14" cy="14" r="7" fill="none" stroke="#0054AA" stroke-width="2"/><path d="M14 10v4l3 2" fill="none" stroke="#0054AA" stroke-width="2"/></svg>
    <div><b>OPEN HOURS</b>Mon to Sat - 9:00 AM to 6:00 PM</div>
  </div>
  <div class="contact-btn">CONTACT</div>
</header>

<nav class="mainnav">
  <div class="brand">Brightlane<br>Rapid Rinse</div>
  <div class="navlinks">
    <span>Home</span><span>About us</span><span>Why Brightlane</span><span>Services and pricing</span><span>Videos of wash system</span><span>Fleets</span>
  </div>
</nav>

<section class="hero">
  <div class="hero-photo" role="img" aria-label="Truck inside an automated wash bay with red and black rotating brushes, glass facility on the left"></div>
  <div class="hero-copy">
    <div class="kicker">WELCOME TO</div>
    <h1>BRIGHTLANE<br>RAPID RINSE</h1>
    <div class="tag">SPEED (LESS THAN 15 MINUTES) AND QUALITY</div>
  </div>
  <div class="abs btn btn-white" style="left:111px;top:399px;width:166px;height:39px">BOOK A WASH</div>
  <div class="abs btn btn-white" style="left:307px;top:399px;width:169px;height:39px">LEARN MORE</div>
  <div class="play"><svg width="30" height="30" viewBox="0 0 30 30"><circle cx="15" cy="15" r="14" fill="#0054AA"/><path d="M12 9l9 6-9 6z" fill="#fff"/></svg></div>
</section>

<section class="about">
  <h2 class="sec-title" style="top:58px">About Us</h2>
  <div class="rule" style="top:114px"></div>
  <p>Lorem ipsum dolor sit amet, consectetur adipiscing elit, sed do eiusmod tempor incididunt ut labore et dolore magna aliqua. Ut enim ad minim veniam, quis nostrud exercitation ullamco laboris nisi ut aliquip ex ea commodo consequat. Duis aute irure dolor in reprehenderit in voluptate velit esse cillum dolore eu fugiat nulla pariatur. Excepteur sint occaecat cupidatat non proident, sunt in culpa qui officia deserunt mollit anim id est laborum.Sed ut perspiciatis unde omnis iste natus error sit voluptatem accusantium doloremque laudantium.</p>
  <div class="abs btn btn-blue" style="left:517px;top:356px;width:166px;height:39px">LEARN MORE</div>
</section>

<section class="services" role="img" aria-label="Blue tinted photo of a worker washing vehicles outdoors">
  <h2 class="sec-title light" style="top:56px">Our Services</h2>
  <div class="rule light" style="top:115px"></div>

  <div class="card" style="left:68px">
    <div class="photo" role="img" aria-label="Truck trailer inside a white wash bay" style="background:linear-gradient(90deg,#cfd4da 0%,#e9ecef 50%,#d6c24a 75%,#c43a30 90%,#5aa14a 100%)"></div>
    <div class="badge"><svg width="40" height="40" viewBox="0 0 40 40" fill="none" stroke="#fff" stroke-width="2"><path d="M6 8h28M10 8v4M20 8v4M30 8v4"/><rect x="9" y="16" width="22" height="14" rx="2"/><circle cx="14" cy="32" r="3"/><circle cx="26" cy="32" r="3"/></svg></div>
    <h3>AUTOMATED TRUCK WASH</h3><div class="bar"></div>
    <p>Lorem ipsum dolor sit amet, consectetur adipiscing elit, sed do eiusmod tempor incididunt ut labore et dolore magna.</p>
    <div class="more">LEARN MORE <svg width="26" height="12" viewBox="0 0 26 12"><path d="M0 6h24M19 1l5 5-5 5" fill="none" stroke="#0054AA" stroke-width="2"/></svg></div>
  </div>

  <div class="card" style="left:442px">
    <div class="photo" role="img" aria-label="Oil being poured into an engine" style="background:radial-gradient(circle at 45% 55%,#d99a2b 0%,#6b4a22 30%,#1e1f22 70%)"></div>
    <div class="badge"><svg width="40" height="40" viewBox="0 0 40 40" fill="none" stroke="#fff" stroke-width="2"><rect x="10" y="12" width="9" height="20" rx="1"/><rect x="22" y="16" width="9" height="16" rx="1"/><path d="M14 12V7h3M26 16v-4"/></svg></div>
    <h3>ADDITIONAL SERVICES</h3><div class="bar"></div>
    <p>Lorem ipsum dolor sit amet, consectetur adipiscing elit, sed do eiusmod tempor incididunt ut labore et dolore magna.</p>
    <div class="more">LEARN MORE <svg width="26" height="12" viewBox="0 0 26 12"><path d="M0 6h24M19 1l5 5-5 5" fill="none" stroke="#0054AA" stroke-width="2"/></svg></div>
  </div>

  <div class="card" style="left:814px">
    <div class="photo" role="img" aria-label="Row of white fleet trucks parked under an evening sky" style="background:linear-gradient(180deg,#8b9bb2 0%,#c7ccd4 45%,#e7e8ea 65%,#6a6f78 100%)"></div>
    <div class="badge"><svg width="40" height="40" viewBox="0 0 40 40" fill="none" stroke="#fff" stroke-width="2"><rect x="8" y="9" width="24" height="20" rx="2"/><path d="M8 18h24M13 13h14"/><circle cx="14" cy="32" r="3"/><circle cx="26" cy="32" r="3"/></svg></div>
    <h3>FLEET SERVICES</h3><div class="bar"></div>
    <p>Lorem ipsum dolor sit amet, consectetur adipiscing elit, sed do eiusmod tempor incididunt ut labore et dolore magna.</p>
    <div class="more">LEARN MORE <svg width="26" height="12" viewBox="0 0 26 12"><path d="M0 6h24M19 1l5 5-5 5" fill="none" stroke="#0054AA" stroke-width="2"/></svg></div>
  </div>

  <div class="abs btn btn-white" style="left:517px;top:649px;width:166px;height:39px">VIEW MORE</div>
</section>

<section class="beforeafter">
  <div class="ba-photo" style="left:0;background:linear-gradient(180deg,#6d7e98 0%,#d88a4a 35%,#8d8a88 60%,#3b3a3c 100%)" role="img" aria-label="Dirty cement truck at sunset"></div>
  <div class="ba-photo" style="left:600px;background:linear-gradient(90deg,#b0324a 0%,#4a5a8a 8%,#8c929c 30%,#c9ccd1 50%,#8c929c 70%,#4a5a8a 92%,#b0324a 100%)" role="img" aria-label="Clean bus inside a wash bay"></div>
  <div class="ba-label" style="left:80px">SERVICE BEFORE</div>
  <div class="ba-label" style="left:681px">SERVICE AFTER</div>
</section>

<section class="reviews">
  <h2 class="sec-title" style="top:62px">Client Reviews</h2>
  <div class="rule" style="top:119px"></div>

  <div class="review" style="left:136px">
    <div class="avatar" role="img" aria-label="Client portrait"></div>
    <h4>Lorem ipsum</h4><div class="sub">Lorem ipsum dolor sit .</div>
    <p>Lorem ipsum dolor sit amet, consectetur adipiscing elit, sed do eiusmod tempor incididunt ut labore et dolore adipiscing</p>
    <div class="stars">★★★★★</div>
  </div>
  <div class="review" style="left:470px">
    <div class="avatar" role="img" aria-label="Client portrait"></div>
    <h4>Lorem ipsum</h4><div class="sub">Lorem ipsum dolor sit .</div>
    <p>Lorem ipsum dolor sit amet, consectetur adipiscing elit, sed do eiusmod tempor incididunt ut labore et dolore adipiscing</p>
    <div class="stars">★★★★★</div>
  </div>
  <div class="review" style="left:805px">
    <div class="avatar" role="img" aria-label="Client portrait"></div>
    <h4>Lorem ipsum</h4><div class="sub">Lorem ipsum dolor sit .</div>
    <p>Lorem ipsum dolor sit amet, consectetur adipiscing elit, sed do eiusmod tempor incididunt ut labore et dolore adipiscing</p>
    <div class="stars">★★★★★</div>
  </div>

  <div class="abs btn btn-blue" style="left:517px;top:495px;width:166px;height:39px">VIEW MORE</div>
</section>

<section class="mission">
  <div class="mission-photo" role="img" aria-label="White truck covered in foam inside a wash bay"></div>
  <h2 class="sec-title light" style="top:64px">Our Mission</h2>
  <div class="rule light" style="top:118px"></div>

  <div class="goal" style="top:178px">Lorem ipsum dolor sit amet, consectetur<br>adipiscing elit.  sed do eiusmod.</div>
  <div class="goal-num" style="top:171px">01</div>
  <div class="goal" style="top:269px">Lorem ipsum dolor sit amet, consectetur<br>adipiscing elit.  sed do eiusmod.</div>
  <div class="goal-num" style="top:262px">02</div>
  <div class="goal" style="top:360px">Lorem ipsum dolor sit amet, consectetur<br>adipiscing elit.  sed do eiusmod.</div>
  <div class="goal-num" style="top:353px">03</div>
  <div class="goal" style="top:452px">Lorem ipsum dolor sit amet, consectetur<br>adipiscing elit.  sed do eiusmod.</div>
  <div class="goal-num" style="top:445px">04</div>
</section>

<section class="contact">
  <h2 class="sec-title" style="top:62px">Contact Us</h2>
  <div class="rule" style="top:119px"></div>
  <div class="field" style="left:290px;top:161px;width:270px;height:43px">First Name</div>
  <div class="field" style="left:640px;top:161px;width:270px;height:43px">Last Name</div>
  <div class="field" style="left:290px;top:238px;width:620px;height:43px">Enter Your E-mail Address</div>
  <div class="field" style="left:290px;top:315px;width:620px;height:43px">Enter Your Phone Number</div>
  <div class="field area" style="left:290px;top:399px;width:620px;height:87px">Type Your Message</div>
  <div class="abs btn btn-blue" style="left:488px;top:529px;width:224px;height:45px;font-size:19px">SEND MESSAGE</div>
</section>

<footer class="footer">
  <div class="flogo">Brightlane<br>Rapid Rinse</div>
  <div class="social" style="left:79px"></div>
  <div class="social" style="left:120px"></div>
  <div class="social" style="left:161px"></div>
  <div class="social" style="left:202px"></div>
  <div class="social" style="left:243px"></div>

  <div class="fcol" style="left:363px">
    <h5>OUR SERVICES</h5>
    <ul><li>Cement trucks</li><li>dump trucks</li><li>vac trucks</li><li>fuel trucks etc</li><li>Refrigerator truck</li></ul>
  </div>
  <div class="fcol links" style="left:615px">
    <h5>QUICK LINKS</h5>
    <ul><li>Privacy</li><li>Terms of Use</li><li>Cookie preferences</li><li>Site Map</li><li>Support</li></ul>
  </div>
  <div class="fcontact">
    <h5 style="font:700 23px 'Montserrat',sans-serif">CONTACT US</h5>
    <div class="row" style="top:62px"><div class="ic"><svg width="16" height="16" viewBox="0 0 16 16"><path d="M3 2l3 3-2 2c1 2 3 4 5 5l2-2 3 3-2 2C7 15 1 9 1 4z" fill="#0054AA"/></svg></div><span>+1 555 010 0199</span></div>
    <div class="row" style="top:118px"><div class="ic"><svg width="16" height="16" viewBox="0 0 16 16"><rect x="2" y="4" width="12" height="9" fill="none" stroke="#0054AA" stroke-width="1.6"/><path d="M2 4l6 5 6-5" fill="none" stroke="#0054AA" stroke-width="1.6"/></svg></div><span>rinse.desk@example.com</span></div>
    <div class="row" style="top:170px"><div class="ic"><svg width="16" height="16" viewBox="0 0 16 16"><path d="M8 1a5 5 0 0 0-5 5c0 4 5 9 5 9s5-5 5-9a5 5 0 0 0-5-5z" fill="#0054AA"/><circle cx="8" cy="6" r="2" fill="#fff"/></svg></div><span>Brightlane Rapid Rinse,<br>United States</span></div>
  </div>

  <div class="divider"></div>
  <div class="copy">© 2024  Brightlane Rapid Rinse. All rights reserved.</div>
</footer>

</body>
</html>
```